Harborline Auto LLC

Car Dealer Customer Service
Address: 2874 Cresthaven Road, Shelbyville, TN 37162
web: www.harborlineautoxq.net
email: harborlineautoxq@mailnest.example
Phone: (931) 555-0148
Phone: (629) 555-0173

```html
<!DOCTYPE html>
<html lang="en">
<head>
<meta charset="utf-8">
<title>Harborline Auto — Business Card</title>
<link href="https://fonts.googleapis.com/css2?family=Poppins:wght@400;600;700&display=swap" rel="stylesheet">
<style>
  :root {
    --page: #d9dcde;
    --card: #eef1f2;
    --blue: #1f7a9c;
    --teal-dark: #1b5b73;
    --gold: #e0a52a;
    --ink: #1e2326;
    --white: #ffffff;
  }
  * { margin: 0; padding: 0; box-sizing: border-box; }
  html, body { width: 1200px; height: 1054px; overflow: hidden; }
  body { background: var(--page); font-family: "Poppins", sans-serif; }
  .card {
    position: absolute; left: 100px; top: 241px;
    width: 1000px; height: 571px;
    background: var(--card);
    border-radius: 26px; overflow: hidden;
    box-shadow: 0 10px 30px rgba(0,0,0,.15);
  }
  .card__band {
    position: absolute; left: 0; top: 0; width: 100%; height: 150px;
    background: var(--blue);
  }
  .card__rule {
    position: absolute; left: 0; top: 160px; width: 100%; height: 8px;
    background: var(--gold);
  }
  .phones {
    position: absolute; right: 40px; top: 26px;
    display: flex; flex-direction: column; gap: 4px; align-items: flex-end;
  }
  .phone {
    display: flex; align-items: center; gap: 16px;
    color: var(--white); font-weight: 600; font-size: 36px; letter-spacing: 1px; line-height: 1.2;
  }
  .icon { width: 30px; height: 30px; flex: none; }
  .person { position: absolute; right: 48px; top: 280px; text-align: right; }
  .person__name { color: var(--teal-dark); font-weight: 700; font-size: 36px; line-height: 1.2; }
  .person__role { color: var(--ink); font-size: 25px; line-height: 1.3; }
  .address {
    position: absolute; right: 48px; top: 400px; text-align: right;
    color: var(--ink); font-size: 24px; line-height: 1.35;
  }
  .links {
    position: absolute; right: 40px; top: 486px;
    display: flex; flex-direction: column; gap: 4px; align-items: flex-end;
  }
  .link { display: flex; align-items: center; gap: 14px; color: var(--ink); font-size: 23px; line-height: 1.35; }
  .link .icon { width: 22px; height: 22px; }
  .brand {
    position: absolute; left: 52px; top: 500px;
    display: flex; align-items: center; gap: 14px;
  }
  .brand__dot { width: 22px; height: 22px; border-radius: 50%; background: var(--gold); }
  .brand__name { color: var(--teal-dark); font-weight: 700; font-size: 38px; letter-spacing: .5px; line-height: 1; }
</style>
</head>
<body>
  <div class="card">
    <div class="card__band"></div>
    <div class="card__rule"></div>

    <div class="phones">
      <div class="phone">931-555-0148
        <svg class="icon" viewBox="0 0 24 24" aria-hidden="true"><path d="M3 9c0-3 4-5 9-5s9 2 9 5v2h-5V8.5c-1-.5-6-.5-8 0V11H3z M6 13h12l2 7H4z" fill="var(--white)"/></svg>
      </div>
      <div class="phone">629-555-0173
        <svg class="icon" viewBox="0 0 24 24" aria-hidden="true"><path d="M3 9c0-3 4-5 9-5s9 2 9 5v2h-5V8.5c-1-.5-6-.5-8 0V11H3z M6 13h12l2 7H4z" fill="var(--white)"/></svg>
      </div>
    </div>

    <div class="person">
      <div class="person__name">Darnell Ruffo</div>
      <div class="person__role">Managing Director</div>
    </div>

    <div class="address">
      <div>2874 Cresthaven Road,</div>
      <div>Shelbyville, TN 37162</div>
    </div>

    <div class="links">
      <div class="link">www.harborlineautoxq.net
        <svg class="icon" viewBox="0 0 24 24" aria-hidden="true"><circle cx="12" cy="12" r="9" fill="none" stroke="var(--gold)" stroke-width="2"/><path d="M3 12h18M12 3c3 3 3 15 0 18M12 3c-3 3-3 15 0 18" fill="none" stroke="var(--gold)" stroke-width="2"/></svg>
      </div>
      <div class="link">harborlineautoxq@mailnest.example
        <svg class="icon" viewBox="0 0 24 24" aria-hidden="true"><rect x="2" y="5" width="20" height="14" rx="1" fill="var(--gold)"/><path d="M2 6l10 7 10-7" fill="none" stroke="var(--card)" stroke-width="1.8"/></svg>
      </div>
    </div>

    <div class="brand">
      <span class="brand__dot"></span>
      <span class="brand__name">HARBORLINE AUTO</span>
    </div>
  </div>
</body>
</html>
```